Redgum Ridge Towing website

We need a website design for a towing company based in Australia.
The design should be simple and minimalist. The site can be in colours of the logo are Blue, Red and White (see attached) - but we'd like to see options in some sort of industrial looking metallic theme if possible.
We base our business on our friendly and efficient customer service, the design should attempt to convey this in some way.

```html
<!DOCTYPE html>
<html lang="en">
<head>
<meta charset="utf-8">
<title>Redgum Ridge Towing</title>
<link href="https://fonts.googleapis.com/css2?family=Open+Sans:wght@400;600;700&family=Arimo:wght@400;700&family=Oswald:wght@400&display=swap" rel="stylesheet">
<style>
:root{
  --blue:#0d3f8f;
  --red:#d9101a;
  --ink:#555;
  --muted:#8a8a8a;
  --nav:#d9d9d9;
  --nav-line:#c6c6c6;
  --panel:rgba(45,45,45,.9);
  --field:#e6e6e6;
  --bubble:#8f9196;
  --footer:#e6e4e6;
}
*{box-sizing:border-box;margin:0;padding:0}
html,body{width:929px;height:1200px;overflow:hidden;background:#fff}
body{position:relative;font-family:"Open Sans",Arial,sans-serif;color:var(--ink)}
.abs{position:absolute}
.header{left:0;top:0;width:929px;height:134px;background:linear-gradient(#fbfbfb,#e6e6e6);box-shadow:0 2px 4px rgba(0,0,0,.15)}
.brand{left:80px;top:40px;display:flex;align-items:center;gap:8px;font-size:15px;font-weight:700;color:var(--blue);width:200px;line-height:1.2}
.brand-mark{width:22px;height:22px;border-radius:50%;background:var(--blue);flex:none}
.clock{left:460px;top:21px}
.tagline{left:512px;top:25px;width:150px;text-align:center;font-size:14px;line-height:19px;color:#666}
.address{left:720px;top:19px;font-size:12.5px;line-height:17px;color:#555}
.phone{left:720px;top:52px;font-size:21px;letter-spacing:.5px;color:#555}
.nav{left:279px;top:92px;height:38px;display:flex}
.nav a{display:block;height:38px;line-height:38px;text-align:center;font-size:13.5px;color:#444;text-decoration:none;background:linear-gradient(#e6e6e6,#d0d0d0);border-left:1px solid #f2f2f2;border-right:1px solid var(--nav-line)}
.nav a.active{background:var(--blue);color:#fff;border:none}
.hero{left:78px;top:148px;width:774px;height:323px;background:linear-gradient(180deg,#bcd9ee 0%,#dde9f0 45%,#a3a7ab 70%,#5d5f61 100%)}
.quick{left:630px;top:169px;width:192px;height:284px;background:var(--panel)}
.quick h3{font-family:"Oswald",sans-serif;font-weight:400;color:#fff;font-size:16px;text-align:center;margin-top:11px}
.field{position:absolute;left:13px;width:164px;height:29px;background:var(--field);font-family:Arimo,Arial,sans-serif;font-size:9px;color:#222;font-weight:700;padding:9px 9px}
.field span{font-weight:400;color:#777}
.btn{position:absolute;left:60px;top:234px;width:72px;height:29px;background:var(--red);color:#fff;font-size:12px;text-align:center;line-height:29px}
.dots{left:427px;top:486px;display:flex;gap:8px}
.dots i{width:8px;height:8px;border-radius:50%;background:#999;display:block}
.dots i:first-child{background:var(--red)}
h2{font-weight:400;font-size:19px;color:#555}
h2 em{font-style:normal;color:var(--blue)}
.body{font-family:Arimo,Arial,sans-serif;font-size:10.3px;line-height:14px;color:var(--muted)}
.team{left:78px;top:591px;width:180px;height:138px;background:linear-gradient(120deg,#f2f2f2,#d9d9d9 55%,#b9b9b9)}
.list li{list-style:none;display:flex;align-items:center;gap:10px;margin-bottom:10px}
.list svg{flex:none}
.avatar{width:52px;height:52px;border-radius:50%;border:2px solid #ddd;background:radial-gradient(#d9c0ad,#b89a84)}
.who{font-size:8px;font-weight:700;color:#333;line-height:9px}
.who small{display:block;font-weight:400;font-size:7.5px;color:#333}
.bubble{width:200px;background:var(--bubble);border-radius:3px;color:#fff;font-size:10px;line-height:15.5px;padding:9px 9px;box-shadow:0 2px 0 #c9c9c9}
.bubble:before{content:"";position:absolute;left:-13px;top:9px;border-right:13px solid var(--bubble);border-bottom:13px solid transparent}
.services h2{text-align:center}
.svc{width:228px;text-align:center}
.svc h4{font-weight:400;font-size:14.5px;color:#555;margin:8px 0 12px}
.svc a{display:block;color:var(--red);font-size:11px;margin-top:9px;text-decoration:none}
.footer{left:0;top:1126px;width:929px;height:74px;background:linear-gradient(#eeeaee,#dedcdf)}
.flinks{left:76px;top:1145px;font-size:10.5px;color:#777}
.flinks b{font-weight:400;margin:0 5px;color:#999}
.copy{left:76px;top:1166px;font-size:10.5px;color:#777}
.social{left:762px;top:1147px;display:flex;gap:9px}
.social i{display:block;width:24px;height:24px;border-radius:50%;background:#fff;box-shadow:0 1px 2px rgba(0,0,0,.25)}
.social i:first-child{background:var(--blue)}
</style>
</head>
<body>
<header class="abs header"></header>
<div class="abs brand"><span class="brand-mark"></span>Redgum Ridge Towing</div>
<svg class="abs clock" width="46" height="46" viewBox="0 0 46 46" aria-hidden="true">
  <circle cx="23" cy="23" r="21" fill="#fff" stroke="#111" stroke-width="2.5"/>
  <text x="23" y="28" text-anchor="middle" font-family="Open Sans, sans-serif" font-size="12" font-weight="700" fill="#d9101a">24/7</text>
</svg>
<div class="abs tagline">Emergency 24 hour Towing Service</div>
<div class="abs address">41 Ironbark Road<br>Kelvale, NSW 2790</div>
<div class="abs phone">02 - 55 - 7410</div>
<nav class="abs nav">
  <a class="active" style="width:73px">Home</a>
  <a style="width:101px">About</a>
  <a style="width:105px">Services</a>
  <a style="width:95px">Gallery</a>
  <a style="width:108px">Partners</a>
  <a style="width:91px">Contact</a>
</nav>

<div class="abs hero" role="img" aria-label="Photo of a flatbed tow truck carrying a white pickup"></div>
<form class="abs quick">
  <h3>Quick Contact</h3>
  <div class="field" style="top:41px">Name <span>(required)</span></div>
  <div class="field" style="top:79px">Email <span>(required)</span></div>
  <div class="field" style="top:117px">Phone <span>(required)</span></div>
  <div class="field" style="top:163px;height:56px;padding-top:12px">Your comment <span>(required)</span></div>
  <div class="btn">Contact</div>
</form>
<div class="abs dots"><i></i><i></i><i></i></div>

<h2 class="abs" style="left:78px;top:528px">Why choose <em>US</em></h2>
<div class="abs team" role="img" aria-label="Photo of a smiling business team"></div>
<p class="abs body" style="left:274px;top:588px;width:255px;text-align:justify">established fact that a reader will be distracted by the readable content of a page when looking at its layout. The point of using Lorem Ipsum is that it has a more-or-less normal distribution of letters, as opposed to using 'Content here, content here', making it look like readable English. Many desktop publishing packages and web page editors now use Lorem Ipsum as their default model text, and a Well being of our clients first! search for 'lorem ipsum' will uncover many web sites still in their infancy.</p>
<p class="abs body" style="left:78px;top:743px;width:452px">established fact that a reader will be distracted by the readable content of a page when looking at its layout. The point of using Lorem Ipsum is that it has a more-or-less normal distribution of</p>
<ul class="abs body list" style="left:77px;top:780px">
  <li><svg width="13" height="13" viewBox="0 0 13 13"><circle cx="6.5" cy="6.5" r="5.5" fill="none" stroke="#0d3f8f" stroke-width="1.6"/><path d="M5 4l3.5 2.5L5 9z" fill="#0d3f8f"/></svg>established fact that a reader will be distracted by the readable content of a page</li>
  <li><svg width="13" height="13" viewBox="0 0 13 13"><circle cx="6.5" cy="6.5" r="5.5" fill="none" stroke="#0d3f8f" stroke-width="1.6"/><path d="M5 4l3.5 2.5L5 9z" fill="#0d3f8f"/></svg>established fact that a reader will be distracted by the</li>
</ul>

<h2 class="abs" style="left:569px;top:531px">What people <em>say</em></h2>
<div class="abs avatar" style="left:568px;top:588px" role="img" aria-label="Customer portrait"></div>
<div class="abs who" style="left:569px;top:645px">MARA QUILL<small>CEO, EXAMPLE.NET</small></div>
<div class="abs bubble" style="left:653px;top:590px">Because we know you don't want to be limited on a portrait or scape format we made Showcase.</div>
<div class="abs avatar" style="left:568px;top:696px" role="img" aria-label="Customer portrait"></div>
<div class="abs who" style="left:569px;top:754px">MARA QUILL<small>CEO, EXAMPLE.NET</small></div>
<div class="abs bubble" style="left:653px;top:699px">Because we know you don't want to be limited on a portrait or scape format we made Showcase.</div>

<section class="services">
  <h2 class="abs" style="left:0;width:929px;top:865px">Towing Services</h2>
  <div class="abs svc" style="left:70px;top:914px">
    <svg width="64" height="44" viewBox="0 0 64 44" aria-hidden="true"><path d="M2 4l22 22" stroke="#111" stroke-width="3"/><rect x="4" y="20" width="28" height="14" fill="#111"/><path d="M32 20h14l8 8h6v10H32z" fill="#111"/><circle cx="14" cy="37" r="6" fill="#111" stroke="#fff" stroke-width="2"/><circle cx="48" cy="37" r="6" fill="#111" stroke="#fff" stroke-width="2"/></svg>
    <h4>We tow them all</h4>
    <p class="body">reader will be distracted by the readable content of a page when looking at its layout. The point of using Lorem Ipsum is that it has a more-or-less normal distribution of letters.</p>
    <a>Read More</a>
  </div>
  <div class="abs svc" style="left:352px;top:918px">
    <svg width="40" height="38" viewBox="0 0 40 38" aria-hidden="true"><rect x="2" y="0" width="3" height="38" fill="#111"/><rect x="35" y="0" width="3" height="38" fill="#111"/><rect x="2" y="24" width="36" height="3" fill="#111"/><path d="M10 20l3-8h14l3 8z" fill="#111"/><rect x="9" y="18" width="22" height="5" fill="#111"/></svg>
    <h4>Who we Service</h4>
    <p class="body">reader will be distracted by the readable content of a page when looking at its layout. The point of using Lorem Ipsum is that it has a more-or-less normal distribution of letters.</p>
    <a>Read More</a>
  </div>
  <div class="abs svc" style="left:626px;top:918px">
    <svg width="40" height="38" viewBox="0 0 40 38" aria-hidden="true"><path d="M1 38V2h38v36" fill="none" stroke="#111" stroke-width="2.5"/><path d="M4 7h32M4 11h32M4 15h32" stroke="#111" stroke-width="2"/><path d="M10 30l3-8h14l3 8z" fill="#111"/><rect x="9" y="28" width="22" height="6" fill="#111"/></svg>
    <h4>Large Facility</h4>
    <p class="body">reader will be distracted by the readable content of a page when looking at its layout. The point of using Lorem Ipsum is that it has a more-or-less normal distribution of letters.</p>
    <a>Read More</a>
  </div>
</section>

<footer class="abs footer"></footer>
<div class="abs flinks">Home<b>|</b>About the Group<b>|</b>Divisions<b>|</b>Group Companies<b>|</b>Press Room<b>|</b>Employment &amp; Association<b>|</b>Contact Us</div>
<div class="abs copy">Copyright © 2014 Redgum Ridge Towing All right reserved.</div>
<div class="abs social" aria-label="Social links"><i></i><i></i><i></i></div>
</body>
</html>
```